Bright and beautiful business card for a coach

I'm a personal and business coach based in Perth, Australia. I need a business card that whilst subtle and elegant, will stand out and appeal on a table full of cards.

My business name is Fern Mentoring and the business card must represent the warmth and brightness implied in the name, without being gimmicky. It must have a warmth and appeal and be easy to read.

I prefer clean, minimalist designs.

It must align with the feel of my website and socials: https://www.fernmentoring-example.com.au/
https://www.instagram.com/fernmentoringau/
https://www.facebook.com/fernmentoringau
Updates

Hi Designers Thank you so much for taking the time to submit designs. I wonder if I could have explained myself a little better. Most of the designs that have been submitted look rather formal and many have quite corporate looking embellishments on them (to my eye). I would like softer, warmer, more organic. I’m open to people playing about and being more abstract, using softer embellishments (e.g the line drawing flowers and grasses I’ve used in my socials) incorporating other colours from my palette or like the social icons in my email signature (in PDF), perhaps playing with size/oversize, playing with the bleed. Please don’t be constrained by what I’ve already done, it merely needs to compliment. I’m sorry if I’m not using the right words or have led you astray. I’m no designer, but I’ve done my website, socials, email signature etc all myself (my logo was a design contest) and I was really hoping for my business card to be something more creative than I could have made with a template. Reminder: No black cards/sides please. Thank you 😊

Target Market(s)

Individuals, most likely but not all female. Creative thinkers. Likely professionals.

Industry/Entity Type

Business & Personal Coach

Contact Information for Business Card

(Fern Mentoring Logo) Name: Greta Pellham; Title: Business & Personal Coach; Phone number: +61 (0)458 913307; Email: greta@fernmentoring-example.com.au; Website: https://fernmentoring-example.com.au; Social icons for Facebook, Instagram & LinkedIn: @fernmentoringAU. Optional strapline: "A thinking partner to help you cut through the noise"

Font styles to use
Sans Serif

Colors
00AB8E
00BBA5
67D7C9
C6EFE9
E9F9F6
59FF00
82FF00
B8FF75
E3FFCB
F4FFEA
FFC000
F8CF3A
FAE287
FDF2CF
FEFAEE

Requirements
Must have
• Must align with feel of my website and socials. Must have a pop of #FFC000 (possibly whole of one side, or at least a block). Bright or white background. Easy to read.
Nice to have
• Possibly incorporate the sunshine/grass picture I have used in website and socials - will upload.
Should not have
• Must not be black or dark. Not impersonal or corporate looking.

```html
<!DOCTYPE html>
<html lang="en">
<head>
<meta charset="utf-8">
<title>Fern Mentoring – Business Card</title>
<link href="https://fonts.googleapis.com/css2?family=Montserrat:wght@400;500;600;700&display=swap" rel="stylesheet">
<style>
  :root {
    --sun: #FCC010;
    --sun-light: #FDD04A;
    --ink: #1E1E1E;
    --grey: #5A5A5A;
    --paper: #FFFFFF;
    --page: #FFFFFF;
  }
  * { box-sizing: border-box; margin: 0; padding: 0; }
  html, body {
    width: 687px; height: 1200px; overflow: hidden;
    background: var(--page);
    font-family: "Montserrat", sans-serif;
  }
  .canvas { position: relative; width: 687px; height: 1200px; }

  .card {
    position: absolute; left: 63px;
    width: 560px; height: 320px;
    box-shadow: 0 2px 6px rgba(0,0,0,0.22);
    overflow: hidden;
  }

  /* Front */
  .card-front { top: 250px; background: var(--sun); }
  .card-front .top-band {
    position: absolute; left: 0; top: 0; width: 100%; height: 9px;
    background: var(--sun-light);
  }
  .card-front .brand-name {
    position: absolute; left: 0; right: 0; top: 118px;
    text-align: center; color: var(--paper);
    font-weight: 600; font-size: 40px; letter-spacing: 1px;
  }
  .card-front .front-url {
    position: absolute; left: 0; right: 0; top: 240px;
    text-align: center; color: var(--paper);
    font-weight: 600; font-size: 17px; letter-spacing: 0.6px;
  }

  /* Back */
  .card-back { top: 630px; background: var(--paper); }
  .card-back .brand-name {
    position: absolute; left: 20px; top: 42px;
    color: var(--sun); font-weight: 600; font-size: 26px;
  }
  .card-back .person {
    position: absolute; right: 20px; top: 156px; text-align: right;
  }
  .person-name {
    color: var(--ink); font-weight: 700; font-size: 24px; line-height: 1;
  }
  .divider {
    position: absolute; left: 21px; top: 184px;
    width: 519px; height: 2px; background: var(--sun);
  }
  .person-title {
    position: absolute; right: 19px; top: 192px;
    color: var(--sun); font-weight: 500; font-size: 14px; letter-spacing: 0.6px;
  }
  .contact-list {
    position: absolute; left: 20px; top: 212px; list-style: none;
  }
  .contact-list li {
    display: flex; align-items: center; height: 26.5px;
    color: var(--grey); font-size: 14px; letter-spacing: 0.3px;
  }
  .contact-icon {
    width: 24px; height: 24px; border-radius: 50%;
    background: var(--sun); margin-right: 11px; flex: none;
    display: flex; align-items: center; justify-content: center;
  }
  .contact-icon svg { width: 14px; height: 14px; }
  .contact-list .domain { color: var(--sun); font-weight: 600; }
  .social-links {
    position: absolute; right: 19px; top: 273px; display: flex; gap: 6px;
  }
  .social-dot {
    width: 18px; height: 18px; border-radius: 50%; background: var(--sun);
  }
</style>
</head>
<body>
<main class="canvas">

  <section class="card card-front" aria-label="Card front">
    <div class="top-band"></div>
    <div class="brand-name">Fern Mentoring</div>
    <div class="front-url">fernmentoring-example.com.au</div>
  </section>

  <section class="card card-back" aria-label="Card back">
    <div class="brand-name">Fern Mentoring</div>

    <div class="person"><div class="person-name">Greta Pellham</div></div>
    <div class="divider"></div>
    <div class="person-title">Business &amp; Personal Coach</div>

    <ul class="contact-list">
      <li>
        <span class="contact-icon">
          <svg viewBox="0 0 24 24" fill="none" stroke="#fff" stroke-width="2.2" stroke-linecap="round" stroke-linejoin="round">
            <path d="M5 3h4l2 5-2.5 1.5a11 11 0 0 0 6 6L16 13l5 2v4a2 2 0 0 1-2 2A16 16 0 0 1 3 5a2 2 0 0 1 2-2z"/>
          </svg>
        </span>
        +61 (0)458 913307
      </li>
      <li>
        <span class="contact-icon">
          <svg viewBox="0 0 24 24" fill="none" stroke="#fff" stroke-width="2.2" stroke-linejoin="round">
            <rect x="3" y="5" width="18" height="14" rx="1.5"/>
            <polyline points="3,6 12,13 21,6"/>
          </svg>
        </span>
        greta@fernmentoring-example.com.au
      </li>
      <li>
        <span class="contact-icon">
          <svg viewBox="0 0 24 24" fill="none" stroke="#fff" stroke-width="2">
            <circle cx="12" cy="12" r="9"/>
            <ellipse cx="12" cy="12" rx="4" ry="9"/>
            <line x1="3" y1="12" x2="21" y2="12"/>
          </svg>
        </span>
        www.<span class="domain">fernmentoring-example.com.au</span>
      </li>
    </ul>

    <div class="social-links" aria-label="Social profiles @fernmentoringAU">
      <span class="social-dot" role="img" aria-label="Social profile"></span>
      <span class="social-dot" role="img" aria-label="Social profile"></span>
      <span class="social-dot" role="img" aria-label="Social profile"></span>
    </div>
  </section>

</main>
</body>
</html>
```